Creative Alcoholic Beverage Package Design Needed!

We need a packaging design for a new alcoholic beverage, including the brand name. Flavours will include Sangria and Margarita, and future line extensions as well. Package will be a box (see attached dieline and example of a competitive product) in a 3 liter format. The dimensions of the box need to match the dieline, but we can be creative on the printing of the box. The product inside will be of high-quality, so the design needs to match this
Updates

Need extra days to review

Target Market(s)

25 to 40 year old, 70% female, 30% male

Colors

Designer to choose colors to be used in the design.

Requirements
Must have
• Be attractive, colourful, modern
• clearly mention the flavour, and show the components of the flavour (Sangria : red wine and citrus) - Margarita (mexican inspiration, lime, etc.)
• Have a clear "brand name" along with the flavours
• Mention the quantity (3 liters), alcohol level : 10% alc./vol.

```html
<!DOCTYPE html>
<html lang="en">
<head>
<meta charset="utf-8">
<title>Vinelle – Sangria and Margarita 3 ltr box fronts</title>
<link rel="stylesheet" href="https://fonts.googleapis.com/css2?family=Cormorant+Garamond:wght@500;600&family=Oswald:wght@600&display=swap">
<style>
  :root {
    --stage: #e9eaec;
    --sangria-dark: #2a0508;
    --sangria-mid: #4a0c12;
    --sangria-red: #d4241c;
    --sangria-orange: #e8641c;
    --sangria-amber: #f4a23a;
    --ink-light: #f6eee8;
    --margarita-pale: #e6f0d2;
    --margarita-soft: #c9dfa6;
    --margarita-lime: #8fbf4a;
    --margarita-yellow: #e9d25a;
    --ink-green: #1f4a1a;
  }
  * { margin: 0; padding: 0; box-sizing: border-box; }
  html, body { width: 1200px; height: 1200px; overflow: hidden; }
  body {
    background: var(--stage);
    font-family: "Cormorant Garamond", Georgia, serif;
    position: relative;
  }
  .box-front {
    position: absolute;
    top: 250px;
    width: 480px;
    height: 700px;
    overflow: hidden;
    box-shadow: 0 18px 40px rgba(0,0,0,0.18);
  }
  .box-front--sangria { left: 90px; background: linear-gradient(160deg, var(--sangria-mid), var(--sangria-dark) 60%); color: var(--ink-light); }
  .box-front--margarita { left: 630px; background: linear-gradient(180deg, var(--margarita-pale), var(--margarita-soft)); color: var(--ink-green); }

  .label { position: absolute; top: 70px; left: 0; right: 0; text-align: center; z-index: 2; }
  .brand {
    display: inline-flex; align-items: center; gap: 14px;
    font-size: 72px; font-weight: 500; line-height: 1;
  }
  .brand-dot { width: 14px; height: 14px; border-radius: 50%; background: currentColor; }
  .flavour { margin-top: 34px; font-size: 40px; font-weight: 600; }
  .box-front--sangria .flavour { color: var(--sangria-red); }
  .components { margin-top: 6px; font-size: 28px; font-weight: 500; }

  .visual { position: absolute; left: 0; right: 0; bottom: 0; height: 470px; }
  .visual--sangria {
    border-radius: 50% 50% 0 0 / 22% 22% 0 0;
    background: radial-gradient(ellipse at 45% 45%, var(--sangria-amber), var(--sangria-orange) 45%, var(--sangria-red) 80%, var(--sangria-mid));
  }
  .visual--margarita {
    background: radial-gradient(ellipse at 45% 60%, var(--margarita-yellow), var(--margarita-lime) 55%, var(--margarita-soft));
    opacity: 0.85;
  }

  .strength { position: absolute; left: 26px; bottom: 34px; font-size: 22px; font-weight: 500; z-index: 2; }
  .volume { position: absolute; right: 28px; bottom: 22px; z-index: 2; display: flex; align-items: baseline; gap: 4px; }
  .volume-number { font-family: "Oswald", "Arial Narrow", sans-serif; font-size: 68px; font-weight: 600; line-height: 1; }
  .volume-unit { font-size: 30px; font-weight: 600; }
  .box-front--sangria .volume, .box-front--sangria .strength { color: #ffffff; }
</style>
</head>
<body>
  <section class="box-front box-front--sangria">
    <div class="label">
      <div class="brand"><span>Vinelle</span><span class="brand-dot"></span></div>
      <div class="flavour">Sangria</div>
      <div class="components">Red Wine &amp; Citrus</div>
    </div>
    <div class="visual visual--sangria" role="img" aria-label="Bowl of sangria seen from above with orange and lemon slices, kumquats, pomegranate seeds and star anise"></div>
    <p class="strength">10% alc./vol.</p>
    <p class="volume"><span class="volume-number">3</span><span class="volume-unit">ltr</span></p>
  </section>

  <section class="box-front box-front--margarita">
    <div class="label">
      <div class="brand"><span>Vinelle</span><span class="brand-dot"></span></div>
      <div class="flavour">Margarita</div>
      <div class="components">Mexican Inspiration &amp; Lime</div>
    </div>
    <div class="visual visual--margarita" role="img" aria-label="Glass of margarita with ice cubes, lemon, fresh herbs and a lime wedge, with a green liquid splash"></div>
    <p class="strength">10% alc./vol.</p>
    <p class="volume"><span class="volume-number">3</span><span class="volume-unit">ltr</span></p>
  </section>
</body>
</html>
```